Business Card Design

An energy company designed around renewable energy and energy storage that focuses on providing its energy at points on the grid that reduce costs and add value to the system.

Industry/Entity Type

Business

Contact Information for Business Card

Gavin Kellerby
Executive Vice President
53 K ST NE
Washington, DC 20019
301-555-0187
gkellerby@tallowmereco.com

```html
<!DOCTYPE html>
<html lang="en">
<head>
<meta charset="utf-8">
<title>Business Card – Gavin Kellerby</title>
<link href="https://fonts.googleapis.com/css2?family=Oswald:wght@500;700&display=swap" rel="stylesheet">
<style>
  :root {
    --backdrop: #ecebec;
    --card-edge: #ffffff;
    --card-face: #000000;
    --name-ink: #ffffff;
    --detail-ink: #8a8a8a;
    --icon-ink: #ffffff;
  }
  * { margin: 0; padding: 0; box-sizing: border-box; }
  html, body {
    width: 1200px;
    height: 845px;
    overflow: hidden;
    background: var(--backdrop);
  }
  .canvas {
    width: 1200px;
    height: 845px;
    display: flex;
    align-items: center;
    justify-content: center;
  }
  .business-card {
    width: 840px;
    height: 480px;
    background: var(--card-edge);
    padding: 16px;
    box-shadow: 0 6px 24px rgba(0, 0, 0, 0.12);
  }
  .card-face {
    width: 100%;
    height: 100%;
    background: var(--card-face);
    padding: 110px 0 0 190px;
    font-family: "Oswald", "Arial Narrow", sans-serif;
    text-transform: uppercase;
  }
  .holder-name {
    color: var(--name-ink);
    font-weight: 700;
    font-size: 60px;
    line-height: 1;
    letter-spacing: 0.5px;
  }
  .holder-title {
    color: var(--detail-ink);
    font-weight: 700;
    font-size: 38px;
    line-height: 1;
    letter-spacing: 1px;
    margin-top: 2px;
  }
  .contact-list {
    list-style: none;
    margin-top: 12px;
  }
  .contact-item {
    display: flex;
    align-items: center;
    gap: 10px;
    color: var(--detail-ink);
    font-weight: 500;
    font-size: 25px;
    line-height: 1.3;
    letter-spacing: 0.5px;
  }
  .contact-icon {
    width: 26px;
    height: 26px;
    flex: none;
    fill: var(--icon-ink);
    stroke: var(--icon-ink);
  }
</style>
</head>
<body>
  <main class="canvas">
    <section class="business-card">
      <div class="card-face">
        <h1 class="holder-name">Gavin Kellerby</h1>
        <p class="holder-title">Executive Vice President</p>
        <ul class="contact-list">
          <li class="contact-item">
            <svg class="contact-icon" viewBox="0 0 26 26" aria-hidden="true">
              <circle cx="13" cy="4" r="3" stroke="none"/>
              <path d="M13 8 L13 16 M13 16 L9 24 M13 16 L17 24 M13 10 L8 15 M13 10 L18 15" fill="none" stroke-width="3" stroke-linecap="round"/>
              <rect x="3" y="24" width="20" height="2" stroke="none"/>
            </svg>
            <span>53 K St NE Washington, DC 20019</span>
          </li>
          <li class="contact-item">
            <svg class="contact-icon" viewBox="0 0 26 26" aria-hidden="true">
              <path d="M2 10 Q13 2 24 10 L20 13 L17 10 L17 8 Q13 6 9 8 L9 10 L6 13 Z" stroke="none"/>
              <rect x="5" y="14" width="16" height="9" rx="2" stroke="none"/>
              <circle cx="13" cy="18.5" r="2.5" fill="#000" stroke="none"/>
            </svg>
            <span>301-555-0187</span>
          </li>
          <li class="contact-item">
            <svg class="contact-icon" viewBox="0 0 26 26" aria-hidden="true">
              <rect x="1" y="5" width="24" height="16" stroke="none"/>
              <path d="M1 5 L13 14 L25 5" fill="none" stroke="#000" stroke-width="2"/>
            </svg>
            <span>gkellerby@tallowmereco.com</span>
          </li>
        </ul>
      </div>
    </section>
  </main>
</body>
</html>
```